Stonebridge Building and Projects business cards

A business card with watermark background (construction work)

Company logo attached

Home improvement projects
House renovations
Bathroom and kitchen renovations
House extensions
New builds and granny flats

Director Omar Haddani
(Phone number)
omar@sbpbuilding.com.au
(Instagram logo) sbp_building

```html
<!DOCTYPE html>
<html lang="en">
<head>
<meta charset="utf-8">
<title>Stonebridge Building and Projects – Business Card</title>
<link rel="stylesheet" href="https://fonts.googleapis.com/css2?family=Fira+Sans:wght@500&family=Roboto:wght@400;500&family=Courier+Prime:wght@700&display=swap">
<style>
  :root {
    --page-bg: #e9e6e2;
    --card-top: #f4f3f2;
    --card-bottom: #e4e3e2;
    --brand-blue: #1f78b4;
    --brand-blue-dark: #1a5f8d;
    --name-blue: #1c6fa6;
    --ink: #333a40;
    --rule: #3a3f44;
    --tagline: #e7eef3;
  }
  * { margin: 0; padding: 0; box-sizing: border-box; }
  html, body {
    width: 1200px; height: 1054px; overflow: hidden;
    background: var(--page-bg);
  }
  .card {
    position: absolute; left: 100px; top: 227px;
    width: 1000px; height: 600px;
    border-radius: 28px;
    background: linear-gradient(180deg, var(--card-top), var(--card-bottom));
    box-shadow: 0 12px 40px rgba(0,0,0,0.12);
    overflow: hidden;
  }
  .brand {
    position: absolute; left: 64px; top: 190px; width: 420px;
    display: flex; align-items: flex-start; gap: 18px;
    font-family: "Roboto", sans-serif; font-weight: 500; color: var(--brand-blue);
  }
  .brand-square {
    flex: none; width: 22px; height: 22px; margin-top: 14px;
    background: var(--brand-blue);
  }
  .brand-name { line-height: 1.1; }
  .brand-name .primary { display: block; font-size: 50px; }
  .brand-name .secondary { display: block; font-size: 30px; margin-top: 8px; }
  .person {
    position: absolute; left: 534px; top: 138px;
    font-family: "Fira Sans", sans-serif;
  }
  .person-name { font-size: 36px; font-weight: 500; color: var(--name-blue); }
  .person-role {
    font-family: "Roboto", sans-serif; font-size: 24px; color: var(--ink);
    margin-top: 6px;
  }
  .contacts {
    position: absolute; left: 534px; top: 252px; list-style: none;
    font-family: "Roboto", sans-serif; font-size: 25px; color: var(--ink);
  }
  .contacts li { display: flex; align-items: center; height: 38.5px; }
  .contacts svg { width: 24px; height: 24px; margin-right: 24px; flex: none; }
  .footer-rule {
    position: absolute; left: 0; right: 0; bottom: 77px; height: 4px;
    background: var(--rule);
  }
  .footer-band {
    position: absolute; left: 0; right: 0; bottom: 0; height: 62px;
    background: linear-gradient(180deg, var(--brand-blue), var(--brand-blue-dark));
    display: flex; align-items: center; justify-content: center;
    font-family: "Courier Prime", monospace; font-weight: 700;
    font-size: 27px; color: var(--tagline);
  }
</style>
</head>
<body>
  <div class="card">
    <div class="brand">
      <span class="brand-square"></span>
      <span class="brand-name">
        <span class="primary">Stonebridge</span>
        <span class="secondary">Building and Projects</span>
      </span>
    </div>

    <div class="person">
      <div class="person-name">Omar Haddani</div>
      <div class="person-role">Managing Director</div>
    </div>

    <ul class="contacts">
      <li>
        <svg viewBox="0 0 24 24" fill="none" stroke="#333a40" stroke-width="1.6">
          <circle cx="12" cy="12" r="10"/>
          <path d="M8.5 7.5c.6-.6 1.3-.5 1.6.1l.8 1.6c.2.5 0 1-.4 1.3l-.6.4c.6 1.4 1.6 2.5 3 3.1l.4-.6c.3-.4.8-.6 1.3-.4l1.6.8c.6.3.7 1 .1 1.6-1 1-2.6 1.2-4.3.2-1.6-1-2.9-2.4-3.8-4-.9-1.6-.7-3.1.3-4.1z"/>
        </svg>
        0400 318 762
      </li>
      <li>
        <svg viewBox="0 0 24 24" fill="none" stroke="#333a40" stroke-width="1.6">
          <rect x="2.5" y="5" width="19" height="14" rx="1"/>
          <path d="M3 6l9 7 9-7"/>
        </svg>
        omar@sbpbuilding.com.au
      </li>
      <li>
        <svg viewBox="0 0 24 24" fill="none" stroke="#333a40" stroke-width="1.6">
          <circle cx="12" cy="12" r="10"/>
          <ellipse cx="12" cy="12" rx="4.5" ry="10"/>
          <path d="M2 12h20M4 7h16M4 17h16"/>
        </svg>
        sbpbuilding.com.au
      </li>
      <li>
        <svg viewBox="0 0 24 24">
          <circle cx="12" cy="12" r="9" fill="#c8487a"/>
        </svg>
        sbp_building
      </li>
    </ul>

    <div class="footer-rule"></div>
    <div class="footer-band">Built to last!</div>
  </div>
</body>
</html>
```